Business card design

We need a business card designed completed for a new company. We are a company that works with associations, schools to convert their older text/DVDs into dynamic online and mobile programs. Our initial platform is designed for the legal associations and will enable their lawyers to access their content such as forms, videos, case law and support materials anywhere, anytime. We are also focused on Project Management Associations, Financial Management Associations and IT Associations.

I would like for the business card to have the following information:

Logo

Kent marrowby

President and CEO

kmarrowby@trevantiq.example

Mobile: 555-374-9160

www.trevantiq.example

Tag line: Transforming content into a mobile platform    

I would like it to be double sided, use the colours of the logo, tie into the mobile world

 

Industry/Entity Type

Legal

Logo Text

Trevantiq

```html
<!DOCTYPE html>
<html lang="en">
<head>
<meta charset="utf-8">
<title>Trevantiq business card</title>
<link rel="stylesheet" href="https://fonts.googleapis.com/css2?family=PT+Sans:wght@400;700&display=swap">
<style>
  :root {
    --stage: #7a5538;
    --label: #1f140c;
    --card-grey: #9b9b9b;
    --card-white: #ffffff;
    --band-dark: #666666;
    --ink-light: #ffffff;
    --ink-dark: #555555;
    --ink-soft: #333333;
  }
  * { margin: 0; padding: 0; box-sizing: border-box; }
  html, body { width: 1200px; height: 800px; overflow: hidden; }
  body {
    position: relative;
    background: var(--stage);
    font-family: "PT Sans", sans-serif;
  }
  .side-label {
    position: absolute;
    width: 510px;
    text-align: center;
    font-size: 21px;
    color: var(--label);
  }
  .card {
    position: absolute;
    width: 510px;
    height: 291px;
    border-radius: 18px;
    overflow: hidden;
  }
  .card--grey { background: var(--card-grey); color: var(--ink-light); }
  .card--white { background: var(--card-white); color: var(--ink-soft); }
  .card__band { position: absolute; inset: 0; width: 100%; height: 100%; }
  .card__band .band-dark { fill: var(--band-dark); }
  .card--grey .band-stripe { fill: var(--card-grey); }
  .card--white .band-stripe { fill: var(--card-white); }

  .wordmark { position: absolute; font-weight: 700; line-height: 1; }
  .card--grey .wordmark { color: var(--ink-light); }
  .card--white .wordmark { color: var(--ink-dark); }
  .wordmark--detail { left: 45px; top: 46px; font-size: 62px; }
  .wordmark--hero { left: 0; right: 0; top: 104px; text-align: center; font-size: 82px; }

  .tagline { position: absolute; left: 45px; top: 138px; font-size: 16px; }
  .person { position: absolute; left: 45px; top: 198px; }
  .person__name { font-size: 17px; }
  .person__role { font-size: 13px; margin-top: 2px; }
  .divider { position: absolute; left: 168px; top: 198px; width: 1px; height: 58px; background: currentColor; opacity: .7; }
  .contact { position: absolute; left: 190px; top: 197px; list-style: none; font-size: 14px; line-height: 23px; }
  .web-address {
    position: absolute; left: 0; right: 0; bottom: 16px;
    text-align: center; font-size: 17px; letter-spacing: 3px;
    color: var(--ink-soft);
  }
</style>
</head>
<body>
  <div class="side-label" style="left:80px;top:50px">Front</div>
  <div class="side-label" style="left:634px;top:50px">Back - 1</div>
  <div class="side-label" style="left:73px;top:409px">Back - 2</div>
  <div class="side-label" style="left:634px;top:409px">Back - 3</div>

  <section class="card card--grey" style="left:80px;top:97px">
    <svg class="card__band" viewBox="0 0 510 291" aria-hidden="true">
      <path class="band-dark" d="M355,0 Q505,110 430,291 L510,291 L510,0 Z"/>
      <path class="band-stripe" d="M398,0 Q500,95 478,238 Q488,100 440,0 Z"/>
    </svg>
    <div class="wordmark wordmark--detail">Trevantiq</div>
    <p class="tagline">Transforming content into a mobile platform</p>
    <div class="person">
      <p class="person__name">Kent marrowby</p>
      <p class="person__role">President and CEO</p>
    </div>
    <div class="divider"></div>
    <ul class="contact">
      <li><b><i>c</i></b> : 555-374-9160</li>
      <li>e : kmarrowby@trevantiq.example</li>
      <li>w : www.trevantiq.example</li>
    </ul>
  </section>

  <section class="card card--white" style="left:634px;top:97px">
    <svg class="card__band" viewBox="0 0 510 291" aria-hidden="true">
      <path class="band-dark" d="M355,0 Q505,110 430,291 L510,291 L510,0 Z"/>
      <path class="band-stripe" d="M398,0 Q500,95 478,238 Q488,100 440,0 Z"/>
    </svg>
    <div class="wordmark wordmark--detail">Trevantiq</div>
    <p class="tagline">Transforming content into a mobile platform</p>
    <div class="person">
      <p class="person__name">Kent marrowby</p>
      <p class="person__role">President and CEO</p>
    </div>
    <div class="divider"></div>
    <ul class="contact">
      <li><b><i>c</i></b> : 555-374-9160</li>
      <li>e : kmarrowby@trevantiq.example</li>
      <li>w : www.trevantiq.example</li>
    </ul>
  </section>

  <section class="card card--grey" style="left:73px;top:451px">
    <div class="wordmark wordmark--hero">Trevantiq</div>
    <p class="web-address">www.trevantiq.example</p>
  </section>

  <section class="card card--white" style="left:634px;top:450px">
    <div class="wordmark wordmark--hero">Trevantiq</div>
    <p class="web-address">www.trevantiq.example</p>
  </section>
</body>
</html>
```